New Business Card Design Project

We require a business card design for Vexalund, a newly established Indian company.
Our focus is on the development, manufacturing, and export of a diverse array of pharmaceutical products on a global scale. The card should convey a professional appearance, as our primary markets are in Africa, China, and Southeast Asian nations.
We envision a two-sided business card, with the reverse side dedicated to a logo set against a solid color or an elegantly designed pattern. The corners should be rounded. We would appreciate seeing both horizontal and vertical design options. We trust the designer to utilize their expertise in creating this design.

The content for the business card is included in the attached Word file.

Target Market(s)

Our primary markets are in Africa, China, and Southeast Asian, Latin America, Maldives, Sri Lanka

Industry/Entity Type

Pharmaceutical Manufacturing and Export

Contact Information for Business Card

Colors

Designer to choose colors to be used in the design.

Requirements
Must have
• The reverse side of the business card features solely the logo along with the tagline, "Care Across Borders."
Should not have
• The logo should not exceed two instances, encompassing both the front and back sides of the card.

```html
<!DOCTYPE html>
<html lang="en">
<head>
<meta charset="utf-8">
<title>Vexalund — Business Card</title>
<link rel="stylesheet" href="https://fonts.googleapis.com/css2?family=Montserrat:wght@800&family=Open+Sans:wght@400;600&display=swap">
<style>
  :root {
    --stage: #222222;
    --card-dark: #1d1e21;
    --card-coral: #e05a4a;
    --brand-blue: #2ea6df;
    --brand-coral: #ef5f4c;
    --ink-light: #e9e7e4;
    --ink-muted: #c9c9cb;
  }
  * { margin: 0; padding: 0; box-sizing: border-box; }
  html, body {
    width: 1200px; height: 780px; overflow: hidden;
    background: var(--stage);
  }
  .stage {
    width: 1200px; height: 780px;
    display: flex; align-items: center; justify-content: center; gap: 50px;
  }
  .card {
    position: relative;
    width: 525px; height: 300px;
    border-radius: 22px;
    overflow: hidden;
    box-shadow: 0 14px 30px rgba(0,0,0,0.45);
  }

  /* Front */
  .card-front { background: var(--card-dark); }
  .front-wordmark {
    position: absolute; left: 36px; top: 34px;
    font-family: "Montserrat", sans-serif; font-weight: 800;
    font-size: 40px; letter-spacing: -0.5px; line-height: 1.2;
    color: var(--brand-blue);
  }
  .address {
    position: absolute; left: 38px; top: 104px;
    font-family: "Open Sans", sans-serif; font-size: 11.5px; line-height: 1.45;
    color: var(--ink-muted);
  }
  .contact-list {
    position: absolute; left: 38px; top: 152px;
    list-style: none;
    font-family: "Open Sans", sans-serif; font-size: 11.5px; line-height: 1.9;
    color: var(--ink-muted);
  }
  .contact-list li { display: flex; align-items: center; gap: 8px; white-space: nowrap; }
  .contact-list svg { width: 12px; height: 12px; flex: none; }
  .holder {
    position: absolute; right: 62px; top: 104px; text-align: right;
    font-family: "Open Sans", sans-serif; white-space: nowrap;
  }
  .holder-name { font-size: 22px; font-weight: 400; line-height: 1.3; color: var(--brand-coral); }
  .holder-name .given { font-weight: 600; color: var(--brand-blue); }
  .holder-role { font-size: 13px; color: var(--ink-light); margin-top: 2px; letter-spacing: 0.5px; }
  .edge-tab {
    position: absolute; right: 0; top: 112px;
    width: 36px; height: 40px;
    background: var(--brand-blue);
  }
  .edge-tab::after {
    content: ""; position: absolute; left: -12px; top: 26px;
    width: 12px; height: 14px; background: var(--brand-blue);
  }

  /* Back */
  .card-back {
    background: var(--card-coral);
    display: flex; flex-direction: column; align-items: center; justify-content: center;
  }
  .back-lockup { display: flex; flex-direction: column; align-items: flex-start; }
  .back-wordmark {
    font-family: "Montserrat", sans-serif; font-weight: 800;
    font-size: 58px; letter-spacing: -0.5px; line-height: 1.2;
    color: var(--ink-light);
  }
  .tagline {
    margin-top: 4px; margin-left: 4px;
    font-family: "Open Sans", sans-serif; font-size: 14px;
    color: var(--ink-light);
  }
</style>
</head>
<body>
<main class="stage">
  <section class="card card-front" aria-label="Business card front">
    <div class="front-wordmark">Vexalund</div>
    <p class="address">14, Sunbird Colony,<br>Nashik, 422001, India</p>
    <ul class="contact-list">
      <li>
        <svg viewBox="0 0 12 12" aria-hidden="true"><rect x="2.5" y="0.8" width="7" height="10.4" rx="1.2" fill="none" stroke="var(--brand-coral)" stroke-width="1.2"/></svg>
        +919000041275
      </li>
      <li>
        <svg viewBox="0 0 12 12" aria-hidden="true"><circle cx="6" cy="6" r="5" fill="none" stroke="var(--brand-blue)" stroke-width="1.2"/><path d="M1 6h10M6 1c-2.4 2.8-2.4 7.2 0 10M6 1c2.4 2.8 2.4 7.2 0 10" fill="none" stroke="var(--brand-blue)" stroke-width="1"/></svg>
        www.vexalund.com
      </li>
      <li>
        <svg viewBox="0 0 12 12" aria-hidden="true"><rect x="0.8" y="2.2" width="10.4" height="7.6" rx="1" fill="none" stroke="var(--brand-coral)" stroke-width="1.2"/><path d="M1 2.8l5 4 5-4" fill="none" stroke="var(--brand-coral)" stroke-width="1.1"/></svg>
        amehrotra@vexalund.com
      </li>
    </ul>
    <div class="holder">
      <p class="holder-name"><span class="given">Arjun</span> K. Mehrotra</p>
      <p class="holder-role">CEO</p>
    </div>
    <div class="edge-tab" aria-hidden="true"></div>
  </section>

  <section class="card card-back" aria-label="Business card back">
    <div class="back-lockup">
      <div class="back-wordmark">Vexalund</div>
      <p class="tagline">Care Across Borders.</p>
    </div>
  </section>
</main>
</body>
</html>
```